Roofing Company Modern look

I want a modern and sophisticated look for our roofing business.

Our address is :

5217 Mallow Creek Ln
Orlando, Fl 32825

(407)-583-2196

www.HarborlineRoofsFl.com

I also want to make sure on the back there is a spot to put
Project Manager Name :

Number:

Because the cards will be used by all sales people

Project Manager Name :

Also there are accreditation we have logos are uploaded here as well that I would like maybe on the back of card as well

I also want to highlight our special attributions or trades:

Residential & Commercial
Fully Insured
License # CCC7482913
Insurance Claims
Serving Central Florida Since 1992
Free Estimates

Contact Information for Business Card

Our address is :

5217 Mallow Creek Ln
Orlando, Fl 32825

(407)-583-2196

Project Manager Name :

Residential & Commercial
Fully Insured
License # CCC7482913
Insurance Claims
Free Estimates

Font styles to use
Serif
Sans Serif

Colors
3176b5

Requirements
Must have
• Must have royal blue like my logo grey and black are the colors I like

```html
<!DOCTYPE html>
<html lang="en">
<head>
<meta charset="utf-8">
<title>Harborline Roofing &amp; Gutters – Business Card</title>
<link rel="stylesheet" href="https://fonts.googleapis.com/css2?family=Arimo:wght@400;700&display=swap">
<style>
  :root {
    --royal-blue: #3176b5;
    --sky-blue: #3a9ee0;
    --deep-blue: #1f5fa8;
    --grey: #98999d;
    --light-grey: #b5b6b9;
    --badge-fill: #d7dbe1;
    --ink: #1e1e1e;
    --paper: #ffffff;
    --backdrop: #e9eaec;
  }
  * { box-sizing: border-box; margin: 0; padding: 0; }
  html, body { width: 1200px; height: 900px; overflow: hidden; }
  body {
    background: var(--backdrop);
    font-family: "Arimo", Arial, sans-serif;
    position: relative;
  }
  .card {
    position: absolute;
    left: 250px;
    width: 700px;
    height: 400px;
    background: var(--paper);
    box-shadow: 0 6px 18px rgba(0,0,0,0.18);
    overflow: hidden;
  }
  .card--back { top: 40px; }
  .card--front { top: 470px; }

  /* Back side */
  .name-field {
    position: absolute;
    left: 130px; top: 70px;
    width: 470px;
    display: flex;
    align-items: flex-end;
    gap: 12px;
  }
  .name-field__label {
    color: var(--light-grey);
    font-weight: 700;
    font-size: 18px;
    letter-spacing: 1px;
  }
  .name-field__line {
    flex: 1;
    border-bottom: 1.5px solid var(--light-grey);
    margin-bottom: 5px;
  }
  .trades {
    position: absolute;
    left: 0; right: 0; top: 120px;
    text-align: center;
    color: var(--royal-blue);
    font-size: 21px;
    line-height: 30px;
    letter-spacing: 0.5px;
  }
  .trades__sep {
    display: inline-block;
    width: 0; height: 0;
    border-left: 6px solid transparent;
    border-right: 6px solid transparent;
    border-bottom: 11px solid #555;
    margin: 0 12px;
    vertical-align: 1px;
  }
  .badges {
    position: absolute;
    left: 0; right: 0; bottom: 44px;
    display: flex;
    justify-content: center;
    align-items: center;
    gap: 34px;
  }
  .badge {
    background: var(--badge-fill);
    border-radius: 8px;
  }
  .badge--wide { width: 150px; height: 72px; }
  .badge--long { width: 190px; height: 54px; }
  .badge--tall { width: 84px; height: 88px; }

  /* Front side */
  .address {
    position: absolute;
    left: 70px; top: 80px;
    color: var(--ink);
    font-size: 24px;
    line-height: 31px;
    font-style: normal;
  }
  .brand {
    position: absolute;
    right: 50px; top: 120px;
    display: flex;
    align-items: center;
    gap: 12px;
  }
  .brand__dot {
    width: 34px; height: 34px;
    border-radius: 50%;
    background: var(--royal-blue);
  }
  .brand__name {
    color: var(--royal-blue);
    font-weight: 700;
    font-size: 22px;
    letter-spacing: 1px;
    line-height: 26px;
    text-transform: uppercase;
  }
  .contact {
    position: absolute;
    left: 70px; top: 200px;
    list-style: none;
    color: var(--ink);
    font-size: 23px;
    line-height: 34px;
  }
  .contact li { display: flex; align-items: center; gap: 10px; }
  .contact svg { width: 20px; height: 20px; flex: none; }
  .wave { position: absolute; left: 0; bottom: 0; width: 700px; height: 220px; }
</style>
</head>
<body>

<section class="card card--back" aria-label="Card back">
  <div class="name-field">
    <span class="name-field__label">NAME:</span>
    <span class="name-field__line"></span>
  </div>
  <p class="trades">
    Residential &amp; Commercial<span class="trades__sep"></span>Fully Insured<br>
    License # CCC7482913<span class="trades__sep"></span>Insurance Claims<br>
    Serving Central Florida Since 1992<span class="trades__sep"></span>Free Estimates
  </p>
  <div class="badges">
    <div class="badge badge--wide" role="img" aria-label="Shingle applicator certification badge"></div>
    <div class="badge badge--long" role="img" aria-label="Authorized roofing contractor badge"></div>
    <div class="badge badge--tall" role="img" aria-label="Accredited business rating badge"></div>
  </div>
</section>

<section class="card card--front" aria-label="Card front">
  <address class="address">
    5217 Mallow Creek Ln<br>
    Orlando, Fl 32825
  </address>

  <div class="brand">
    <span class="brand__dot"></span>
    <span class="brand__name">Harborline Roofing<br>&amp; Gutters Inc.</span>
  </div>

  <ul class="contact">
    <li>
      <svg viewBox="0 0 24 24" aria-hidden="true"><path fill="var(--royal-blue)" d="M6.6 10.8a15.1 15.1 0 0 0 6.6 6.6l2.2-2.2c.3-.3.7-.4 1-.2 1.1.4 2.3.6 3.6.6.6 0 1 .4 1 1V20c0 .6-.4 1-1 1A17 17 0 0 1 3 4c0-.6.4-1 1-1h3.5c.6 0 1 .4 1 1 0 1.3.2 2.5.6 3.6.1.3 0 .7-.2 1z"/></svg>
      (407)-583-2196
    </li>
    <li>
      <svg viewBox="0 0 24 24" aria-hidden="true" fill="none" stroke="var(--royal-blue)" stroke-width="1.8"><circle cx="12" cy="12" r="9.5"/><ellipse cx="12" cy="12" rx="4" ry="9.5"/><path d="M2.5 12h19M4 7h16M4 17h16"/></svg>
      www.HarborlineRoofsFl.com
    </li>
  </ul>

  <svg class="wave" viewBox="0 0 700 220" preserveAspectRatio="none" aria-hidden="true">
    <defs>
      <linearGradient id="waveBlue" x1="0" y1="0" x2="1" y2="0">
        <stop offset="0" stop-color="var(--royal-blue)"/>
        <stop offset="1" stop-color="var(--sky-blue)"/>
      </linearGradient>
    </defs>
    <path d="M0 124 C230 120 390 100 540 40 C600 16 660 8 700 6 V220 H0 Z" fill="var(--grey)"/>
    <path d="M0 144 C250 139 420 114 560 54 C620 29 660 19 700 14 V220 H0 Z" fill="var(--paper)"/>
    <path d="M0 152 C250 147 420 122 560 62 C620 37 660 27 700 22 V220 H0 Z" fill="url(#waveBlue)"/>
  </svg>
</section>

</body>
</html>
```